New Business Card for Web Design/Internet Marketing Company

Looking for a great looking new business card. We are a 10 year old web design, internet marketing and website management company that works mostly with small businesses.

Our new card needs to better match the colors and style of our website, be bold, extremely usable and slightly edgy.

Target Market(s)

Small/Medium businesses that have websites

Industry/Entity Type

Internet

Requirements
Must have
• Front and back design, full color, rounded corners please

Must use the colors/style of our website (JPG provided)

INFO FOR CARDS (as readable as possible please)
Mark Lenner
President/CEO
mark@trelvanmedia.example
Phone: 520-381-7459
Toll Free: 866-381-7459
Address: 4315 W. Calloway Ave. Ste. 140, Tucson, AZ 85792

THINGS I WANT TO PROMOTE (if there is room):
1. Our Website - www.trelvanmedia.example

2. Social Media
Twitter: @trelvanmedia
Facebook: www.facebook.com/trelvanmedia

3. Our Services
Web Design
Internet Marketing
Website Management

```html
<!DOCTYPE html>
<html lang="en">
<head>
<meta charset="utf-8">
<title>Trelvan Media – Business Card</title>
<link rel="stylesheet" href="https://fonts.googleapis.com/css2?family=Open+Sans:wght@400;600;700&display=swap">
<style>
  :root {
    --stage: #e9e6e2;
    --card-white: #ffffff;
    --band-grey: #5f5f5f;
    --back-grey: #626262;
    --faint-grey: #6e6e6e;
    --accent-orange: #f47b20;
    --brand-blue: #1b8fc9;
    --text-grey: #555555;
    --rule-grey: #b5b5b5;
    --white: #ffffff;
  }
  * { margin: 0; padding: 0; box-sizing: border-box; }
  html, body { width: 1200px; height: 402px; overflow: hidden; }
  body {
    background: var(--stage);
    font-family: "Open Sans", Arial, sans-serif;
    position: relative;
  }
  .card {
    position: absolute;
    top: 57px;
    width: 512px;
    height: 292px;
    border-radius: 26px;
    overflow: hidden;
  }
  .card-front { left: 60px; background: var(--card-white); }
  .card-back { left: 625px; background: var(--back-grey); }

  .front-wave { position: absolute; inset: 0; }
  .holder {
    position: absolute; right: 38px; top: 12px;
    text-align: right; color: var(--white);
  }
  .holder-name { font-size: 19px; font-weight: 700; line-height: 1.25; }
  .holder-title { font-size: 12px; font-weight: 400; }

  .brand {
    position: absolute; left: 36px; top: 130px;
    display: flex; align-items: center; gap: 8px;
  }
  .brand-dot {
    width: 20px; height: 20px; border-radius: 50%;
    background: var(--accent-orange);
  }
  .brand-name {
    font-size: 28px; font-weight: 700; color: var(--brand-blue);
    letter-spacing: -0.5px;
  }

  .contact-list {
    position: absolute; left: 36px; top: 206px;
    list-style: none; font-size: 12px; color: var(--text-grey);
  }
  .contact-list li {
    display: flex; align-items: center; gap: 7px; height: 18.5px;
  }
  .contact-icon { width: 10px; height: 10px; flex: none; }
  .address {
    position: absolute; left: 236px; top: 244px;
    padding-left: 14px; border-left: 1px solid var(--rule-grey);
    font-size: 12px; color: var(--text-grey); line-height: 18px;
  }

  .back-decoration { position: absolute; inset: 0; }
  .back-brand {
    position: absolute; left: 30px; top: 160px;
    font-size: 44px; font-weight: 700; color: var(--white);
    letter-spacing: -1px;
  }
  .social-list {
    position: absolute; left: 272px; top: 40px;
    list-style: none; color: var(--white); font-size: 15px;
  }
  .social-list li { display: flex; align-items: center; gap: 10px; height: 23px; }
  .social-mark { width: 15px; height: 15px; background: var(--brand-blue); border-radius: 2px; }
  .services { position: absolute; left: 272px; top: 118px; color: var(--white); }
  .services-title { font-size: 23px; font-weight: 600; margin-bottom: 12px; }
  .services-list { list-style: none; font-size: 20px; line-height: 30.5px; }
</style>
</head>
<body>

<section class="card card-front">
  <svg class="front-wave" viewBox="0 0 512 292" aria-hidden="true">
    <path d="M0,0 H512 V76 C440,80 360,70 280,50 C200,30 110,22 0,58 Z" fill="var(--band-grey)"/>
    <path d="M0,72 C110,30 200,40 280,58 C360,76 440,86 512,80 L512,88 C440,94 360,86 280,66 C200,48 110,40 0,80 Z" fill="var(--accent-orange)"/>
  </svg>
  <div class="holder">
    <div class="holder-name">Mark Lenner</div>
    <div class="holder-title">President/CEO</div>
  </div>
  <div class="brand">
    <span class="brand-dot"></span>
    <span class="brand-name">Trelvan Media</span>
  </div>
  <ul class="contact-list">
    <li><svg class="contact-icon" viewBox="0 0 10 10"><circle cx="5" cy="5" r="5" fill="var(--brand-blue)"/><path d="M3,2.5 L4.2,2.5 L4.6,4 L3.9,4.5 C4.3,5.4 4.8,6 5.6,6.2 L6.1,5.5 L7.5,5.9 L7.5,7.1 C5,7.4 2.7,5.2 3,2.5Z" fill="#fff"/></svg>520-381-7459</li>
    <li><svg class="contact-icon" viewBox="0 0 10 10"><circle cx="5" cy="5" r="5" fill="var(--brand-blue)"/><path d="M3,2.5 L4.2,2.5 L4.6,4 L3.9,4.5 C4.3,5.4 4.8,6 5.6,6.2 L6.1,5.5 L7.5,5.9 L7.5,7.1 C5,7.4 2.7,5.2 3,2.5Z" fill="#fff"/></svg>866-381-7459</li>
    <li><svg class="contact-icon" viewBox="0 0 10 10"><rect x="0" y="2" width="10" height="7" rx="1" fill="var(--brand-blue)"/><path d="M0.5,2.5 L5,6 L9.5,2.5" stroke="#fff" stroke-width="0.8" fill="none"/></svg>mark@trelvanmedia.example</li>
    <li><svg class="contact-icon" viewBox="0 0 10 10"><circle cx="5" cy="5" r="5" fill="var(--brand-blue)"/><path d="M0,5 H10 M5,0 C2.5,3 2.5,7 5,10 M5,0 C7.5,3 7.5,7 5,10" stroke="#fff" stroke-width="0.6" fill="none"/></svg>www.trelvanmedia.example</li>
  </ul>
  <address class="address" style="font-style:normal">
    4315 W. Calloway Ave., Ste. 140<br>Tucson, AZ 85792
  </address>
</section>

<section class="card card-back">
  <svg class="back-decoration" viewBox="0 0 512 292" aria-hidden="true">
    <circle cx="255" cy="150" r="120" fill="none" stroke="var(--faint-grey)" stroke-width="26"/>
  </svg>
  <div class="back-brand">Trelvan</div>
  <ul class="social-list">
    <li><span class="social-mark"></span>@trelvanmedia</li>
    <li><span class="social-mark"></span>trelvanmedia</li>
  </ul>
  <div class="services">
    <h2 class="services-title">Our Services</h2>
    <ul class="services-list">
      <li>Web Design</li>
      <li>Internet Marketing</li>
      <li>Website Management</li>
    </ul>
  </div>
</section>

</body>
</html>
```